New Business Card for Software Company

We are looking at rebranding a 10 year old company that specializes in PDF and DWF solutions for Architects and Engineers. We will attach the new company logo that we are going with so you can work with that and complimentary colors.
The sample information we would like on the business card is:
Gerald Pinfold
Vice President
4738 W. Harrowgate Lane. STE 305
PMB#417
Mesa, AZ 85374
866-392-5074 US Toll Free
123-456-3190 Cell
gpinfold@plavorix.com
The old tag line that we had on the business cars was.
Dependable PDF and DWF Tools Built for Architects and Engineers Everywhere.
If you have an idea for a better tag line we are open to that also.
Updates
We would like to thank all of the Designers for their wonderful work. We apologize that we will not have the time to provide feedback to everyone. There is just so many innovative and professional designs that you have all created making our decision even harder.
Target Market(s)
Architects and Engineers
Industry/Entity Type
Business
Look and feel

```html
<!DOCTYPE html>
<html lang="en">
<head>
<meta charset="utf-8">
<title>Plavorix Business Card</title>
<link rel="stylesheet" href="https://fonts.googleapis.com/css2?family=Arimo:wght@400;700&family=Open+Sans:wght@400&display=swap">
<style>
  :root {
    --page-bg: #e4e3ea;
    --card-bg: #ffffff;
    --brand-orange: #e8561f;
    --ink-grey: #5a5a5a;
    --text-dark: #333333;
    --rule-grey: #bdbdbd;
    --card-shadow: rgba(40, 40, 60, 0.22);
  }
  * { margin: 0; padding: 0; box-sizing: border-box; }
  html, body {
    width: 1200px;
    height: 987px;
    overflow: hidden;
    background: var(--page-bg);
    font-family: "Arimo", Arial, sans-serif;
  }
  .canvas { position: relative; width: 1200px; height: 987px; }
  .card {
    position: absolute;
    width: 720px;
    height: 411px;
    background: var(--card-bg);
    border-radius: 34px;
    box-shadow: 0 14px 30px var(--card-shadow);
    overflow: hidden;
  }

  /* Back of card */
  .card-back { left: 400px; top: 70px; }
  .card-back .brand-name {
    position: absolute;
    left: 70px;
    top: 90px;
    font-size: 128px;
    font-weight: 700;
    letter-spacing: -3px;
    color: var(--brand-orange);
    line-height: 1;
  }
  .card-back .tagline {
    position: absolute;
    left: 76px;
    top: 250px;
    width: 560px;
    font-family: "Open Sans", Arial, sans-serif;
    font-size: 20px;
    line-height: 1.35;
    color: var(--ink-grey);
    text-align: left;
  }

  /* Front of card */
  .card-front { left: 80px; top: 500px; }
  .brand-lockup {
    position: absolute;
    left: 40px;
    top: 34px;
    display: flex;
    align-items: center;
    gap: 14px;
  }
  .brand-dot {
    width: 78px;
    height: 78px;
    border-radius: 50%;
    background: var(--brand-orange);
    flex: none;
  }
  .brand-lockup .brand-name {
    font-size: 96px;
    font-weight: 700;
    letter-spacing: -2px;
    color: var(--brand-orange);
    line-height: 1;
  }
  .person {
    position: absolute;
    right: 40px;
    top: 150px;
    text-align: right;
  }
  .person-name {
    font-size: 30px;
    font-weight: 700;
    color: var(--brand-orange);
  }
  .person-title {
    margin-top: 4px;
    font-size: 21px;
    color: var(--ink-grey);
  }
  .divider {
    position: absolute;
    left: 0;
    top: 226px;
    width: 100%;
    height: 2px;
    background: linear-gradient(90deg, rgba(189,189,189,0) 0%, var(--rule-grey) 35%, var(--rule-grey) 100%);
  }
  .contact-list {
    position: absolute;
    left: 40px;
    top: 250px;
    list-style: none;
    font-size: 19px;
    color: var(--text-dark);
  }
  .contact-list li {
    display: flex;
    align-items: center;
    gap: 10px;
    margin-bottom: 12px;
  }
  .contact-list svg { width: 17px; height: 17px; flex: none; }
  .address {
    position: absolute;
    right: 40px;
    top: 250px;
    text-align: right;
    font-style: normal;
    font-size: 21px;
    line-height: 1.35;
    color: var(--text-dark);
  }
</style>
</head>
<body>
<main class="canvas">

  <section class="card card-back" aria-label="Card back">
    <div class="brand-name">Plavorix</div>
    <p class="tagline">Dependable PDF and DWF Tools Built for<br>Architects and Engineers Everywhere</p>
  </section>

  <section class="card card-front" aria-label="Card front">
    <div class="brand-lockup">
      <span class="brand-dot"></span>
      <span class="brand-name">Plavorix</span>
    </div>

    <div class="person">
      <div class="person-name">Gerald Pinfold</div>
      <div class="person-title">Vice President</div>
    </div>

    <div class="divider"></div>

    <ul class="contact-list">
      <li>
        <svg viewBox="0 0 20 20" aria-hidden="true"><circle cx="10" cy="10" r="9" fill="none" stroke="#e8561f" stroke-width="1.6"/><path d="M7 5.5c-1 .8-1.2 2.2.2 4.4s3 3.6 4.4 4c.9.2 1.6-.3 2-.9l-1.8-1.6-1.2.7c-.8-.4-1.8-1.5-2.2-2.3l.6-1.2z" fill="#e8561f"/></svg>
        866-392-5074(US) TF
      </li>
      <li>
        <svg viewBox="0 0 20 20" aria-hidden="true"><rect x="5" y="2" width="10" height="16" rx="2" fill="none" stroke="#e8561f" stroke-width="1.8"/><rect x="7.5" y="4.5" width="5" height="6" fill="#e8561f"/><circle cx="10" cy="14.5" r="1.2" fill="#e8561f"/></svg>
        123-456-3190
      </li>
      <li>
        <svg viewBox="0 0 20 20" aria-hidden="true"><rect x="2" y="4" width="16" height="12" rx="1.5" fill="#e8561f"/><path d="M2.5 5l7.5 6 7.5-6" fill="none" stroke="#fff" stroke-width="1.5"/></svg>
        gpinfold@plavorix.com
      </li>
    </ul>

    <address class="address">
      4738 W. Harrowgate Lane<br>
      STE 305<br>
      PMB#417, Mesa, AZ 85374
    </address>
  </section>

</main>
</body>
</html>
```